Ledgerwise Forge - WordPress Theme & Logo

Design a logo and Wordpress website design for Ledgerwise Forge. Ledgerwise Forge provides cryptocurrency development services to clients who need a team to create & continue developing a new cryptocurrency or who want to replace their current cryptocurrency development team. more details in the attached document.
Updates

Target Market(s)

Entrepreneurs who are building a business / platform that makes use of an underlying cryptocurrency.

Logo Text

LF or Ledgerwise Forge

Coding

Coded - Design and coding required

Font styles to use
Sans Serif

Requirements
Must have
• Professional logo, complete coded Wordpress theme for all pages, containing all specified links and buttons
Nice to have
• It would be nice if the buttons that are meant to integrate with Dealtrail contain the necessary code for that. I can provide any necessary Dealtrail details from my account.
Should not have
• Slow loading time

```html
<!DOCTYPE html>
<html lang="en">
<head>
<meta charset="utf-8">
<title>Ledgerwise Forge – Cryptocurrency Development</title>
<link href="https://fonts.googleapis.com/css2?family=Montserrat:wght@500;600;700;800&family=Roboto:wght@400;500;700&display=swap" rel="stylesheet">
<style>
:root{
  --navy:#0d1a33;
  --navy-deep:#081226;
  --blue:#1a82f0;
  --steel:#2a5590;
  --steel-dark:#1f4476;
  --accent:#3f8fd8;
  --ink:#111;
  --text:#333;
  --muted:#555;
  --line:#e2e2e2;
  --soft:#f6f6f6;
  --white:#fff;
}
*{margin:0;padding:0;box-sizing:border-box}
html,body{width:1200px;height:3320px;overflow:hidden}
body{position:relative;font-family:'Roboto',sans-serif;color:var(--text);background:var(--white)}
.abs{position:absolute}
.heading{font-family:'Montserrat',sans-serif;font-weight:700;color:var(--ink)}
.center{text-align:center}

/* header */
.hero{left:0;top:0;width:1200px;height:678px;background:
  radial-gradient(ellipse at 60% 55%,#3f8fe0 0%,#1b4ca8 35%,#0c1f55 70%,#061033 100%)}
.topbar{left:0;top:0;width:1200px;height:72px;background:rgba(8,18,38,.55)}
.brand{display:flex;align-items:center;gap:12px;color:var(--white);font-family:'Montserrat',sans-serif;font-weight:600;font-size:20px}
.brand-mark{width:34px;height:34px;background:var(--white)}
.nav-link{top:26px;color:var(--white);font-size:15px;font-weight:500;letter-spacing:.2px}
.lang{left:763px;top:25px;width:34px;height:20px;background:#2f4b9a;border:2px solid #c83030}
.btn{display:flex;align-items:center;justify-content:center;border-radius:30px;font-weight:700;font-size:16px;color:var(--white);background:var(--blue)}
.hero-title{left:0;top:118px;width:1200px;color:var(--white);font-size:34px;line-height:42px;font-weight:700}
.hero-sub{left:200px;top:212px;width:800px;color:var(--white);font-size:12.5px;line-height:25px}
.next{left:100px;top:626px;color:var(--white);font-size:17px}
.counter{left:218px;top:600px;color:var(--white);font-family:'Montserrat',sans-serif;font-weight:700;font-size:62px}

/* section headings */
.eyebrow-dot{width:28px;height:28px;border-radius:50%;background:linear-gradient(135deg,#7fb0e6,#1f4476)}
.eyebrow{font-size:11.5px;color:var(--accent);letter-spacing:.3px;font-weight:500}
.section-title{font-size:38px}

/* features */
.feature{width:321px;height:304px;border:1px solid var(--line);background:var(--white)}
.feature .hex{position:absolute;left:109px;top:39px}
.feature h3{position:absolute;top:176px;width:100%;font-family:'Montserrat',sans-serif;font-weight:700;font-size:27px;color:var(--ink)}
.feature p{position:absolute;top:219px;left:30px;right:30px;font-size:15.5px;line-height:25px;color:var(--text)}

/* about */
.about{left:0;top:1281px;width:1200px;height:467px;background:linear-gradient(120deg,#1f4476,#2c5d98)}
.about-photo{left:102px;top:1347px;width:450px;height:343px;background:linear-gradient(110deg,#d8dde3 0%,#9aa6b6 45%,#2d4670 70%,#cfd6dd 100%)}
.about-label{left:634px;top:1374px;color:var(--white);font-size:11.5px;font-weight:500}
.about-title{left:634px;top:1390px;color:var(--white);font-size:37px}
.about-copy{left:634px;top:1450px;width:470px;color:var(--white);font-size:14.3px;line-height:27.5px}
.btn-outline{left:634px;top:1609px;width:155px;height:45px;border:2px solid var(--white);border-radius:30px;color:var(--white);font-weight:700;font-size:16px;display:flex;align-items:center;justify-content:center}

/* testimonials */
.reviews{left:0;top:1748px;width:1200px;height:523px;background:var(--soft)}
.review{width:322px;height:221px;background:var(--white);top:1968px;box-shadow:0 2px 6px rgba(0,0,0,.04)}
.review .name{position:absolute;top:53px;width:100%;font-family:'Montserrat',sans-serif;font-weight:700;font-size:13.5px;color:var(--ink);letter-spacing:.4px}
.review .stars{position:absolute;top:70px;width:100%;font-size:10px;color:#f3b21b;letter-spacing:1px}
.review p{position:absolute;top:93px;left:20px;right:20px;font-size:13px;line-height:22.8px;color:var(--muted)}
.avatar{top:1927px;width:96px;height:84px}
.quote{top:2164px;width:46px;height:46px}

/* services */
.services-copy{left:180px;top:2441px;width:840px;font-size:14.3px;line-height:27.5px;color:var(--muted)}
.plan{top:2583px;width:317px;height:299px;background:var(--white);box-shadow:0 2px 8px rgba(0,0,0,.06)}
.plan-head{position:absolute;left:0;top:0;width:100%;height:86px;background:linear-gradient(135deg,#5c9ee6,#2b5894 65%,#1f4476);display:flex;align-items:center;justify-content:center;text-align:center;color:var(--white);font-family:'Montserrat',sans-serif;font-weight:800;font-size:25px;line-height:26px}
.plan ul{position:absolute;left:72px;top:111px;list-style:none}
.plan li{font-size:15.5px;line-height:31px;color:var(--text);display:flex;align-items:center;gap:10px}
.plan li::before{content:"";width:9px;height:9px;border-radius:50%;background:var(--accent);box-shadow:0 0 0 2px var(--white),0 0 0 3.5px var(--accent)}
.plan .btn{position:absolute;left:68px;top:222px;width:175px;height:46px}

/* footer */
.footer{left:0;top:2966px;width:1200px;height:354px;background:linear-gradient(180deg,#14223d,#0a1428)}
.footer-mark{left:175px;top:3040px;width:90px;height:90px;background:var(--white)}
.footer-brand{left:98px;top:3172px;width:220px;color:var(--white);font-family:'Montserrat',sans-serif;font-weight:500;font-size:22px}
.social{top:3216px;width:20px;height:20px;border-radius:50%;background:var(--white)}
.col-title{top:3032px;color:var(--white);font-family:'Montserrat',sans-serif;font-weight:700;font-size:17px}
.col-links{top:3070px;list-style:none;color:var(--white);font-size:15px;line-height:33px}
.email{left:808px;top:3069px;width:289px;height:49px;border-radius:30px;background:var(--white);color:#666;font-size:14px;padding-left:24px;display:flex;align-items:center}
.subscribe{left:808px;top:3128px;width:289px;height:48px;font-size:15.5px;letter-spacing:.3px}
.rule{left:100px;top:3256px;width:1000px;height:1px;background:#4a5878}
.copyright{left:0;top:3279px;width:1200px;color:var(--white);font-size:14.5px}
</style>
</head>
<body>

<!-- hero -->
<section class="abs hero" role="img" aria-label="Night city skyline with glowing network lines and a businessman seen from behind"></section>
<header class="abs topbar"></header>
<div class="abs brand" style="left:97px;top:19px"><span class="brand-mark"></span>Ledgerwise Forge</div>
<a class="abs nav-link" style="left:339px">ABOUT US</a>
<a class="abs nav-link" style="left:440px">OUR SERVICES</a>
<a class="abs nav-link" style="left:571px">TESTIMONIALS</a>
<a class="abs nav-link" style="left:705px">BLOG</a>
<span class="abs lang" role="img" aria-label="English language"></span>
<a class="abs btn" style="left:825px;top:8px;width:273px;height:52px">Schedule a Free Consultation</a>

<h1 class="abs hero-title heading center" style="color:var(--white)">YOUR OWN CRYPTOCURRENCY. SECURE,<br>EASY TO USE, &amp; BUILT BY AN EXPERT TEAM.</h1>
<p class="abs hero-sub center">Ledgerwise Forge adds professionalism to cryptocurrency development. Our done-for-you service covers everything from development<br>and IT operations to ongoing support. You have access to a full team, for less than the typical cost of a single developer</p>
<a class="abs btn" style="left:463px;top:268px;width:274px;height:53px">Schedule a Free Consultation</a>

<div class="abs next">Next
  <svg width="26" height="14" viewBox="0 0 26 14" style="vertical-align:middle;margin-left:6px"><path d="M1 7h23M17 1l7 6-7 6" stroke="#fff" stroke-width="1.6" fill="none"/></svg>
</div>
<div class="abs counter">01<span style="font-weight:500;font-size:40px">/</span></div>
<svg class="abs" style="left:312px;top:622px" width="30" height="30" viewBox="0 0 30 30"><circle cx="15" cy="15" r="13" stroke="#fff" stroke-width="1.6" fill="none"/><path d="M12 9l6 6-6 6" stroke="#fff" stroke-width="1.6" fill="none"/></svg>

<!-- why choose -->
<span class="abs eyebrow-dot" style="left:586px;top:750px"></span>
<div class="abs eyebrow center" style="left:0;top:785px;width:1200px">WHY CHOOSE US</div>
<h2 class="abs heading section-title center" style="left:0;top:805px;width:1200px">Why choose Ledgerwise Forge</h2>

<div class="abs feature center" style="left:100px;top:879px">
  <svg class="hex" width="103" height="116" viewBox="0 0 103 116"><polygon points="51.5,0 103,29 103,87 51.5,116 0,87 0,29" fill="#2b5894"/><path d="M34 50h35l-17.5 24zM34 50l7-9h21l7 9M45 50l6.5 24 6.5-24" stroke="#fff" stroke-width="2" fill="none" stroke-linejoin="round"/></svg>
  <h3>Value</h3>
  <p>A team of experts, regular updates, and fixed costs</p>
</div>
<div class="abs feature center" style="left:440px;top:879px">
  <svg class="hex" width="103" height="116" viewBox="0 0 103 116"><polygon points="51.5,0 103,29 103,87 51.5,116 0,87 0,29" fill="#2b5894"/><circle cx="48" cy="58" r="13" stroke="#fff" stroke-width="2" fill="none"/><path d="M58 36h14v10h-8l-4 4v-4h-2z" stroke="#fff" stroke-width="2" fill="none"/></svg>
  <h3>Support</h3>
  <p>Receive advice and other services, beyond development.</p>
</div>
<div class="abs feature center" style="left:778px;top:879px">
  <svg class="hex" width="103" height="116" viewBox="0 0 103 116"><polygon points="51.5,0 103,29 103,87 51.5,116 0,87 0,29" fill="#2b5894"/><circle cx="51.5" cy="46" r="8" stroke="#fff" stroke-width="2" fill="none"/><path d="M30 78v-8a6 6 0 0 1 12 0v8M61 78v-8a6 6 0 0 1 12 0v8M38 66h27" stroke="#fff" stroke-width="2" fill="none"/></svg>
  <h3>Commitment</h3>
  <p>Enjoy regular updates and new features</p>
</div>

<!-- about -->
<section class="abs about"></section>
<div class="abs about-photo" role="img" aria-label="Smiling businessman in a blue blazer holding a tablet in an office"></div>
<div class="abs about-label">ABOUT US</div>
<h2 class="abs heading about-title" style="color:var(--white)">Who We Are</h2>
<p class="abs about-copy">in addition to creating and enhancing cryptocurrencies for clients, the Ledgerwise Forge team has been running the Nuvrel cryptocurrency since 2017. We prefer long-term relationships, enabling us to deliver the very highest quality and giving you peace of mind that you've got a professional and trustworthy team at your side.</p>
<a class="abs btn-outline">Learn More</a>

<!-- testimonials -->
<section class="abs reviews"></section>
<span class="abs eyebrow-dot" style="left:586px;top:1815px"></span>
<div class="abs eyebrow center" style="left:0;top:1847px;width:1200px">CLIENT REVIEW</div>
<h2 class="abs heading section-title center" style="left:0;top:1862px;width:1200px">Testimonials</h2>

<div class="abs review center" style="left:100px"><div class="name">JOHN SMITH</div><div class="stars">★★★★★</div><p>At vero eos et accusamus etto odio dignissimos ducimus qui blanditiis praesentium voluptatum deleniti atque corrupti qures et quas molestias excepturi sint occaecati</p></div>
<div class="abs review center" style="left:439px"><div class="name">JOHN SMITH</div><div class="stars">★★★★★</div><p>At vero eos et accusamus etto odio dignissimos ducimus qui blanditiis praesentium voluptatum deleniti atque corrupti qures et quas molestias excepturi sint occaecati</p></div>
<div class="abs review center" style="left:778px"><div class="name">JOHN SMITH</div><div class="stars">★★★★★</div><p>At vero eos et accusamus etto odio dignissimos ducimus qui blanditiis praesentium voluptatum deleniti atque corrupti qures et quas molestias excepturi sint occaecati</p></div>

<svg class="abs avatar" style="left:213px" viewBox="0 0 96 84" role="img" aria-label="Client portrait"><polygon points="24,0 72,0 96,42 72,84 24,84 0,42" fill="#6a9cc8"/></svg>
<svg class="abs avatar" style="left:552px" viewBox="0 0 96 84" role="img" aria-label="Client portrait"><polygon points="24,0 72,0 96,42 72,84 24,84 0,42" fill="#d9d4cf"/></svg>
<svg class="abs avatar" style="left:891px" viewBox="0 0 96 84" role="img" aria-label="Client portrait"><polygon points="24,0 72,0 96,42 72,84 24,84 0,42" fill="#b9bec4"/></svg>

<svg class="abs quote" style="left:238px" viewBox="0 0 46 46"><circle cx="23" cy="23" r="23" fill="#3a6db0"/><path d="M14 28c0-6 2-9 6-11M25 28c0-6 2-9 6-11" stroke="#fff" stroke-width="4" stroke-linecap="round" fill="none"/><circle cx="17" cy="28" r="3.5" fill="#fff"/><circle cx="28" cy="28" r="3.5" fill="#fff"/></svg>
<svg class="abs quote" style="left:577px" viewBox="0 0 46 46"><circle cx="23" cy="23" r="23" fill="#3a6db0"/><path d="M14 28c0-6 2-9 6-11M25 28c0-6 2-9 6-11" stroke="#fff" stroke-width="4" stroke-linecap="round" fill="none"/><circle cx="17" cy="28" r="3.5" fill="#fff"/><circle cx="28" cy="28" r="3.5" fill="#fff"/></svg>
<svg class="abs quote" style="left:916px" viewBox="0 0 46 46"><circle cx="23" cy="23" r="23" fill="#3a6db0"/><path d="M14 28c0-6 2-9 6-11M25 28c0-6 2-9 6-11" stroke="#fff" stroke-width="4" stroke-linecap="round" fill="none"/><circle cx="17" cy="28" r="3.5" fill="#fff"/><circle cx="28" cy="28" r="3.5" fill="#fff"/></svg>

<!-- services -->
<span class="abs eyebrow-dot" style="left:586px;top:2327px"></span>
<div class="abs eyebrow center" style="left:0;top:2363px;width:1200px">OUR SERVICE</div>
<h2 class="abs heading section-title center" style="left:0;top:2376px;width:1200px">What We Do</h2>
<p class="abs services-copy center">Ledgerwise Forge offers more than just development. We provide a complete solution and our clients receive access to expert advice, ongoing support, I.T. operations, mobile wallets, and even the creation of white papers, Our packages can be tailored to suit you to match your requirements or budget, you can simply pick and choose the features you would like. Alternatively, We can create a custom package just for you.</p>

<div class="abs plan" style="left:100px"><div class="plan-head">Blockchain<br>Creation &amp; Launch</div><ul><li>This is a list item</li><li>Another list item</li><li>Yup, another list item</li></ul><a class="btn">Learn More</a></div>
<div class="abs plan" style="left:442px"><div class="plan-head">Basic</div><ul><li>This is a list item</li><li>Another list item</li><li>Yup, another list item</li></ul><a class="btn">Learn More</a></div>
<div class="abs plan" style="left:783px"><div class="plan-head">Mid-range</div><ul><li>This is a list item</li><li>Another list item</li><li>Yup, another list item</li></ul><a class="btn">Learn More</a></div>

<!-- footer -->
<footer class="abs footer"></footer>
<span class="abs footer-mark"></span>
<div class="abs footer-brand center">Ledgerwise Forge</div>
<span class="abs social" style="left:138px" aria-label="Social link"></span>
<span class="abs social" style="left:182px" aria-label="Social link"></span>
<span class="abs social" style="left:223px" aria-label="Social link"></span>
<span class="abs social" style="left:262px" aria-label="Social link"></span>

<div class="abs col-title" style="left:357px">Site Content</div>
<ul class="abs col-links" style="left:357px"><li>Home</li><li>About</li><li>Feature</li><li>Pricing</li><li>Contact</li></ul>
<div class="abs col-title" style="left:581px">Major Topics</div>
<ul class="abs col-links" style="left:581px"><li>Search</li><li>T&amp;Cs</li><li>Privacy</li><li>Commu</li></ul>
<div class="abs col-title" style="left:808px">Get our Newsletter</div>
<div class="abs email">Enter your email</div>
<a class="abs btn subscribe">SUBSCRIBE</a>
<div class="abs rule"></div>
<div class="abs copyright center">Copyright © 2021 Ledgerwise Forge. All rights reserved.</div>

</body>
</html>
```